Vantor Ridge needs a Business Card Design

We need a business card design for an Information Technology company based in Fairfax Virginia called Vantor Ridge. We want the business card to use our logo colors. We need it to be double-sided. The business card needs to look professional but we would like it to be unique. You can get company information from our web site (http://www.vantorridgellc.example).

Target Market(s)

Target market is Government Agencies and Business Professionals.

Industry/Entity Type

Business

Requirements
Must have
• Must have section for company name, company address, company URL, employee name, title, phone and email. Also must have company logo and space for entering logos.

```html
<!DOCTYPE html>
<html lang="en">
<head>
<meta charset="utf-8">
<title>Vantor Ridge — Business Cards</title>
<link rel="stylesheet" href="https://fonts.googleapis.com/css2?family=Open+Sans:wght@400;600;700&display=swap">
<style>
  :root {
    --navy: #2b3990;
    --navy-deep: #1f2a78;
    --sky: #1175bd;
    --white: #ffffff;
    --mist: #ececec;
    --stage: #1c1c1c;
  }
  * { margin: 0; padding: 0; box-sizing: border-box; }
  html, body { width: 1200px; height: 1024px; overflow: hidden; }
  body { background: var(--stage); font-family: "Open Sans", Arial, sans-serif; position: relative; }

  .card { position: absolute; width: 540px; height: 310px; background: var(--white); overflow: hidden; }
  .card svg.shapes { position: absolute; inset: 0; width: 100%; height: 100%; }
  .card > div, .card > p { position: absolute; }

  .col-left { left: 46px; }
  .col-right { left: 618px; }
  .row-1 { top: 30px; }
  .row-2 { top: 368px; }
  .row-3 { top: 698px; }

  .brand { display: flex; align-items: center; gap: 10px; }
  .brand-square { width: 40px; height: 40px; background: var(--navy); flex: none; }
  .brand-name { font-weight: 700; font-size: 30px; line-height: 1; color: var(--navy); letter-spacing: 0.2px; white-space: nowrap; }
  .brand-tagline { font-size: 9px; font-weight: 600; color: var(--navy); letter-spacing: 0.2px; margin-top: 3px; white-space: nowrap; }
  .brand.on-dark .brand-name, .brand.on-dark + .brand-tagline { color: var(--white); }

  .holder-name { font-weight: 700; font-size: 14px; color: var(--sky); letter-spacing: 0.3px; white-space: nowrap; }
  .holder-title { font-weight: 700; font-size: 10px; color: var(--navy); letter-spacing: 0.3px; }

  .details { color: var(--white); font-size: 13px; line-height: 17px; }
  .details .line { display: flex; align-items: center; gap: 6px; white-space: nowrap; }
  .details svg { width: 11px; height: 11px; fill: var(--white); flex: none; }
  .details .gap { height: 9px; }

  .card > p.url { right: 16px; color: var(--white); font-size: 13px; white-space: nowrap; }
  .large .details { font-size: 15px; line-height: 18px; }
  .large > p.url { font-size: 14px; right: 14px; }
</style>
</head>
<body>

<svg width="0" height="0" style="position:absolute">
  <defs>
    <symbol id="icon-home" viewBox="0 0 12 12"><path d="M6 1 L11.5 6 H10 V11 H7.2 V8 H4.8 V11 H2 V6 H0.5 Z"/></symbol>
    <symbol id="icon-phone" viewBox="0 0 12 12"><path d="M2.5 0.8 L4.6 0.8 L5.4 3.4 L4 4.4 C4.7 6 6 7.3 7.6 8 L8.6 6.6 L11.2 7.4 L11.2 9.5 C11.2 10.5 10.4 11.2 9.4 11.2 C4.8 10.9 1.1 7.2 0.8 2.6 C0.8 1.6 1.5 0.8 2.5 0.8 Z"/></symbol>
    <symbol id="icon-fax" viewBox="0 0 12 12"><path d="M3 0.8 H9 V3.6 H3 Z M1 4.4 H11 V9 H9.2 V11.2 H2.8 V9 H1 Z M3.8 7.6 V10.2 H8.2 V7.6 Z"/></symbol>
    <symbol id="icon-mail" viewBox="0 0 12 12"><path d="M0.8 2.4 H11.2 V3.2 L6 6.6 L0.8 3.2 Z M0.8 4.4 L6 7.8 L11.2 4.4 V9.6 H0.8 Z"/></symbol>
    <linearGradient id="panel-navy" x1="0" y1="0" x2="1" y2="0">
      <stop offset="0" stop-color="#232f80"/><stop offset="1" stop-color="#2c3a96"/>
    </linearGradient>
    <linearGradient id="mark-area" x1="0" y1="0" x2="1" y2="1">
      <stop offset="0" stop-color="#2b3990"/><stop offset="1" stop-color="#1175bd"/>
    </linearGradient>
  </defs>
</svg>

<!-- Front A -->
<section class="card col-left row-1">
  <svg class="shapes" viewBox="0 0 540 310" preserveAspectRatio="none">
    <rect x="40" y="0" width="150" height="240" fill="var(--mist)" opacity="0.7" role="img" aria-label="Faint brand mark decoration"/>
    <polygon points="130,204 540,204 540,310 80,310" fill="var(--navy)"/>
    <polygon points="330,274 540,274 540,310 316,310" fill="var(--sky)"/>
  </svg>
  <div style="left:210px; top:48px;">
    <div class="brand"><span class="brand-square"></span><span class="brand-name">Vantor Ridge</span></div>
    <p class="brand-tagline" style="padding-left:50px;">TURNING IDEAS INTO WORKING SYSTEMS</p>
  </div>
  <p class="holder-name" style="left:148px; top:164px;">DANIEL MORROW</p>
  <p class="holder-title" style="left:148px; top:184px;">JOB TITLE</p>
  <div class="details" style="left:130px; top:210px;">
    <div class="line"><svg><use href="#icon-home"/></svg>4810 Linden Crest Ave, Suite 210&nbsp;&nbsp;&nbsp;Fairfax, VA 22030</div>
    <div class="gap"></div>
    <div class="line"><svg><use href="#icon-phone"/></svg>877.555.0142</div>
    <div class="line"><svg><use href="#icon-fax"/></svg>888.555.0176</div>
    <div class="line"><svg><use href="#icon-mail"/></svg>name@domainname.com</div>
  </div>
  <p class="url" style="top:282px;">www.vantorridgellc.example</p>
</section>

<!-- Front B -->
<section class="card col-right row-1">
  <svg class="shapes" viewBox="0 0 540 310" preserveAspectRatio="none">
    <rect x="0" y="0" width="170" height="240" fill="var(--mist)" opacity="0.7" role="img" aria-label="Faint brand mark decoration"/>
    <polygon points="130,204 540,204 540,310 82,310" fill="var(--navy)"/>
    <polygon points="330,274 540,274 540,310 316,310" fill="var(--sky)"/>
  </svg>
  <div style="left:205px; top:48px;">
    <div class="brand"><span class="brand-square"></span><span class="brand-name">Vantor Ridge</span></div>
    <p class="brand-tagline" style="padding-left:50px;">TURNING IDEAS INTO WORKING SYSTEMS</p>
  </div>
  <p class="holder-name" style="left:134px; top:180px;">DANIEL MORROW <span class="holder-title">| JOB TITLE</span></p>
  <div class="details" style="left:126px; top:210px;">
    <div class="line"><svg><use href="#icon-home"/></svg>4810 Linden Crest Ave, Suite 210&nbsp;&nbsp;&nbsp;Fairfax, VA 22030</div>
    <div class="gap" style="height:5px"></div>
    <div class="line"><svg><use href="#icon-phone"/></svg>877.555.0142</div>
    <div class="line"><svg><use href="#icon-fax"/></svg>888.555.0176</div>
    <div class="line"><svg><use href="#icon-mail"/></svg>name@domainname.com</div>
  </div>
  <p class="url" style="top:282px;">www.vantorridgellc.example</p>
</section>

<!-- Back A -->
<section class="card col-left row-2">
  <svg class="shapes" viewBox="0 0 540 310" preserveAspectRatio="none">
    <rect width="540" height="310" fill="url(#panel-navy)"/>
    <rect x="0" y="0" width="296" height="310" fill="url(#mark-area)" opacity="0.55" role="img" aria-label="Large brand mark decoration"/>
    <polygon points="334,276 540,276 540,310 316,310" fill="var(--sky)"/>
  </svg>
  <div style="left:300px; top:158px;">
    <div class="brand on-dark"><span class="brand-name">Vantor Ridge</span></div>
    <p class="brand-tagline" style="color:var(--white);">TURNING IDEAS INTO WORKING SYSTEMS</p>
  </div>
  <p class="url" style="top:284px;">www.vantorridgellc.example</p>
</section>

<!-- Front C -->
<section class="card col-right row-2 large">
  <svg class="shapes" viewBox="0 0 540 310" preserveAspectRatio="none">
    <polygon points="76,204 540,204 540,310 20,310" fill="var(--navy)"/>
    <polygon points="340,268 540,268 540,310 322,310" fill="var(--sky)"/>
  </svg>
  <div style="left:190px; top:46px;">
    <div class="brand"><span class="brand-square" style="width:46px;height:46px;"></span><span class="brand-name" style="font-size:34px;">Vantor Ridge</span></div>
    <p class="brand-tagline" style="padding-left:56px; font-size:10px;">TURNING IDEAS INTO WORKING SYSTEMS</p>
  </div>
  <p class="holder-name" style="left:106px; top:178px; font-size:15px;">DANIEL MORROW <span class="holder-title" style="font-size:11px;">| JOB TITLE</span></p>
  <div class="details" style="left:94px; top:212px;">
    <div class="line"><svg><use href="#icon-home"/></svg>4810 Linden Crest Ave, Suite 210 | Fairfax, VA 22030</div>
    <div class="gap" style="height:6px"></div>
    <div class="line"><svg><use href="#icon-phone"/></svg>877.555.0142</div>
    <div class="line"><svg><use href="#icon-fax"/></svg>888.555.0176</div>
    <div class="line"><svg><use href="#icon-mail"/></svg>name@domainname.com</div>
  </div>
  <p class="url" style="top:279px;">www.vantorridgellc.example</p>
</section>

<!-- Back B -->
<section class="card col-left row-3">
  <svg class="shapes" viewBox="0 0 540 310" preserveAspectRatio="none">
    <rect x="310" y="20" width="200" height="240" fill="var(--mist)" opacity="0.7" role="img" aria-label="Faint brand mark decoration"/>
    <polygon points="330,270 540,270 540,310 312,310" fill="var(--sky)"/>
  </svg>
  <div style="left:112px; top:124px;">
    <div class="brand"><span class="brand-square"></span><span class="brand-name">Vantor Ridge</span></div>
    <p class="brand-tagline" style="padding-left:50px;">TURNING IDEAS INTO WORKING SYSTEMS</p>
  </div>
  <p class="url" style="top:280px;">www.vantorridgellc.example</p>
</section>

<!-- Back C -->
<section class="card col-right row-3">
  <svg class="shapes" viewBox="0 0 540 310" preserveAspectRatio="none">
    <rect x="0" y="0" width="296" height="310" fill="url(#mark-area)" role="img" aria-label="Large brand mark decoration"/>
    <polygon points="340,270 540,270 540,310 322,310" fill="var(--sky)"/>
  </svg>
  <div style="left:306px; top:152px;">
    <div class="brand"><span class="brand-name">Vantor Ridge</span></div>
    <p class="brand-tagline">TURNING IDEAS INTO WORKING SYSTEMS</p>
  </div>
  <p class="url" style="top:280px;">www.vantorridgellc.example</p>
</section>

</body>
</html>
```